Tovimar Community Development Planning New web site

Design a new web site. I have a budget of $1,500.00.
Attached on PowerPoint is a complete site plan. Home page and linked pages.
10 - 12 pages. All copy and photos will be supplied. (300dpi)
I have shown them the concept which they like.
No data bases required. Home page with animations dissolving.
They former web site has been taken down. They have been in business 30 years in New Jersey
Colors teal blues and greens
There will be a new logo)being designed)
The text in home page copy will give you a detailed story what they are all about.

files have been approved for Tovimar, Inc.   Brenton is the designer

```html
<!DOCTYPE html>
<html lang="en">
<head>
<meta charset="utf-8">
<title>Tovimar, Inc. — Community Development Planning</title>
<link href="https://fonts.googleapis.com/css2?family=Arimo:wght@400;700&family=Tinos:ital,wght@0,400;1,400&display=swap" rel="stylesheet">
<style>
:root{
  --blue:#1a8fc4;
  --blue-dark:#1479ae;
  --text:#4a4a4a;
  --muted:#666;
  --nav-top:#4a4a4a;
  --nav-bot:#2a2a2a;
  --line:#d6d6d6;
  --box-bg:#fafafa;
  --serif:'Tinos', 'Times New Roman', serif;
  --sans:'Arimo', Arial, sans-serif;
}
*{box-sizing:border-box;margin:0;padding:0}
html,body{width:821px;height:1200px;overflow:hidden;background:#fff}
body{position:relative;font-family:var(--sans);color:var(--text)}
.abs{position:absolute}
a{color:var(--blue);text-decoration:none}

.brand{left:94px;top:24px;border-left:2px solid #f3eccb;padding-left:0}
.brand-name{font-family:var(--serif);font-size:27px;color:#111;line-height:30px}
.brand-tag{font-family:var(--serif);font-size:13px;color:#222;line-height:16px}

.hours{left:384px;top:36px;display:flex;gap:8px;align-items:flex-start}
.hours-title{font-family:var(--serif);font-style:italic;font-size:14.5px;color:var(--blue)}
.hours-time{font-family:var(--serif);font-size:10px;color:#222;margin-top:2px}

.signup{left:601px;top:42px;width:129px;height:27px;background:linear-gradient(#2399d0,#1683b9);border-radius:2px;color:#fff;font-size:10px;display:flex;align-items:center;justify-content:center;gap:7px}

.nav{left:94px;top:87px;width:636px;height:29px;background:linear-gradient(var(--nav-top),var(--nav-bot));display:flex;align-items:center;padding-left:36px;gap:0}
.nav span{color:#fff;font-size:8.6px;margin-right:42px}

.hero{left:94px;top:121px;width:636px;height:260px;background:linear-gradient(#8d968f 0%,#b7bcb3 45%,#6d6558 62%,#8a7c63 75%,#7d7868 100%)}
.cap{left:94px;background:rgba(40,40,40,.82);color:#fff;font-size:10.5px;padding:0 13px;height:30px;line-height:30px}
.arrows{left:680px;top:351px;display:flex;gap:2px}
.arrows div{width:19px;height:19px;background:rgba(90,90,90,.7);display:flex;align-items:center;justify-content:center}

.welcome{left:0;width:821px;top:400px;text-align:center;font-family:var(--serif);font-style:italic;font-size:20px;color:var(--blue)}
.intro{left:100px;width:621px;top:434px;text-align:center;font-family:var(--serif);font-style:italic;font-size:9.3px;line-height:17px;color:var(--muted)}

.card{top:487px;width:196px}
.card-img{height:103px}
.card h3{font-weight:400;font-size:11.8px;color:var(--blue);margin:13px 0 8px 1px}
.card p{font-size:7.3px;line-height:14px;color:var(--muted);padding-left:1px}
.btn{display:inline-block;margin-top:12px;border:1px solid #c8c8c8;border-radius:2px;background:linear-gradient(#fff,#e6e6e6);font-size:7.5px;color:#777;padding:5px 10px}

.info{left:94px;top:733px;width:636px;height:72px;border:1px solid var(--line);background:var(--box-bg)}
.info p{position:absolute;left:23px;font-family:var(--serif);font-style:italic;font-size:11px;color:#444}
.contact-now{position:absolute;left:518px;top:19px;width:100px;height:32px;border-radius:2px;background:linear-gradient(#2a9fd6,#1680b6);border:1px solid #136f9f;color:#fff;font-size:10.5px;display:flex;align-items:center;justify-content:center}

.results-h{left:95px;top:827px;font-size:11.8px;color:var(--blue)}
.results-img{left:94px;top:858px;width:179px;height:110px;background:linear-gradient(#8fb6e0,#c9dced 70%,#e6e2dc)}
.results-text{left:293px;top:857px;width:420px;font-size:7.3px;line-height:15.3px;color:var(--muted)}
.results-call{left:293px;top:951px;font-family:var(--serif);font-style:italic;font-size:11px;color:var(--muted)}

.footer{left:94px;top:999px;width:636px;height:120px;background:linear-gradient(#ececec,#fff 35px)}
.fcol{top:1027px}
.fcol h4{font-weight:400;font-size:8.3px;color:var(--blue);margin-bottom:8px}
.fcol li{list-style:none;font-size:7.3px;color:var(--muted);line-height:16.5px}
.rule{left:104px;top:1129px;width:611px;border-top:1px solid var(--line)}
.copy{left:106px;top:1146px;font-size:6.8px;color:#555}
.social{left:621px;top:1142px;display:flex;gap:3px}
.social div{width:21px;height:22px}
</style>
</head>
<body>

<div class="abs brand">
  <div class="brand-name">Tovimar, Inc.</div>
  <div class="brand-tag">Community Development Planning</div>
</div>

<div class="abs hours">
  <svg width="30" height="30" viewBox="0 0 30 30" aria-hidden="true">
    <circle cx="15" cy="15" r="13.5" fill="#e8eef2" stroke="#5b7f95" stroke-width="2"/>
    <circle cx="15" cy="15" r="10" fill="#fff" stroke="#9fb5c2"/>
    <path d="M15 8v7l4 3" stroke="#333" stroke-width="1.4" fill="none" stroke-linecap="round"/>
  </svg>
  <div>
    <div class="hours-title">Hours of Operation:</div>
    <div class="hours-time">Monday–Friday, 9:30 a.m.– 4:30 p.m.</div>
  </div>
</div>

<div class="abs signup">Newsletter Signup
  <svg width="9" height="6" viewBox="0 0 9 6" aria-hidden="true"><path d="M1 1l3.5 3.5L8 1" stroke="#fff" stroke-width="1.6" fill="none"/></svg>
</div>

<nav class="abs nav">
  <span>Home</span><span>Our Company</span><span>Services</span><span>Housing Rehab Application</span><span>Affordable Application</span><span style="margin-right:0">Contact Us</span>
</nav>

<div class="abs hero" role="img" aria-label="City skyline with a domed cathedral and a footbridge over a river under cloudy skies"></div>
<div class="abs cap" style="top:297px">TOVIMAR, INC. IS A CITY PLANNING FIRM</div>
<div class="abs cap" style="top:327px">THAT SPECIALIZES IN COMMUNITY DEVELOPMENT</div>
<div class="abs arrows">
  <div><svg width="6" height="9" viewBox="0 0 6 9"><path d="M5 1L1.5 4.5 5 8" stroke="#ddd" fill="none"/></svg></div>
  <div><svg width="6" height="9" viewBox="0 0 6 9"><path d="M1 1l3.5 3.5L1 8" stroke="#ddd" fill="none"/></svg></div>
</div>

<h1 class="abs welcome" style="font-weight:400">Welcome to Tovimar</h1>
<p class="abs intro">Community Development Planning, Housing Rehabilitation Administration, Federal Housing and Urban Renewal Office (FHURO) Program Management, Implementation of Programs under the jurisdiction of the State Council on Fair Housing (SCFH).</p>

<section class="abs card" style="left:94px">
  <div class="card-img" role="img" aria-label="Two smiling women, one younger and one older" style="background:linear-gradient(135deg,#8a5a3c,#d9b08a 55%,#e8dcc0)"></div>
  <h3>Services</h3>
  <p>Tovimar, Inc. is a city planning firm that specializes in community development and housing rehabilitation program planning, design and implementation. We have over twenty years...</p>
  <span class="btn">Read More</span>
</section>
<section class="abs card" style="left:313px">
  <div class="card-img" role="img" aria-label="City towers and harbor at sunset" style="background:linear-gradient(#c98a52,#9a5a34 55%,#2e2220)"></div>
  <h3>Housing Rehab Application</h3>
  <p>Tovimar, Inc. is a city planning firm that specializes in community development and housing rehabilitation program planning, design and implementation. We have over twenty years...</p>
  <span class="btn">Read More</span>
</section>
<section class="abs card" style="left:534px">
  <div class="card-img" role="img" aria-label="Hand signing a form on a clipboard" style="background:linear-gradient(135deg,#dfe6ee,#f4f6f8 50%,#c9d5e2)"></div>
  <h3>Affordable Application</h3>
  <p>Tovimar, Inc. is a city planning firm that specializes in community development and housing rehabilitation program planning, design and implementation. We have over twenty years...</p>
  <span class="btn">Read More</span>
</section>

<div class="abs info">
  <p style="top:18px">To find out more about affordable housing in the state, please visit <a>www.gardenstatehomes.org/afford</a>. (or)</p>
  <p style="top:39px">To find out more about federal housing programs that we administer, please go to <a>www.fedhousingnet.org</a>.</p>
  <div class="contact-now">Contact Now</div>
</div>

<h2 class="abs results-h" style="font-weight:400">Getting Results</h2>
<div class="abs results-img" role="img" aria-label="Group of young people jumping joyfully against the sky"></div>
<p class="abs results-text">At Tovimar, Inc. we not only design income based programs to be supported by federal and state funding, we also implement local programs to benefit people seeking access to affordable housing. Our experienced staff screen applicants for local affordable housing, pre-qualify persons who have applied for housing rehabilitation assistance, and conduct placement lotteries. Through local housing rehabilitation programs, our experienced construction inspectors determine what improvements are required at eligible units based on local building codes and and health and safety issues. For more information about our services,</p>
<p class="abs results-call">Please contact Tovimar today at <a>(555) 204-3816</a> or <a>tovimar@postmail.net</a></p>

<div class="abs footer"></div>
<div class="abs fcol" style="left:118px"><h4>Our Company</h4><ul><li>Bio's</li><li>Photos</li><li>Principal</li><li>Employees</li></ul></div>
<div class="abs fcol" style="left:210px"><h4>Services</h4><ul><li>National Neighborhood Renewal Society</li><li>Garden State Planners Association</li><li>Regional Planning Officers Guild</li><li>State Community Renewal Association</li></ul></div>
<div class="abs fcol" style="left:412px"><h4>Housing Rehab Application</h4><ul><li>Lakewood</li><li>Brick</li><li>Jackson</li><li>Warren</li></ul></div>
<div class="abs fcol" style="left:539px"><h4>Affordable Application</h4><ul><li>Lakewood - Applicable</li><li>Brick - Applicable</li><li>Jackson - Applicable</li><li>Warren - Applicable</li></ul></div>
<div class="abs fcol" style="left:660px"><h4>Contact Us</h4><ul><li>Contact Info</li><li>Directions</li><li>Sliding Map</li></ul></div>

<div class="abs rule"></div>
<p class="abs copy">Copyright © 2014. Tovimar. All rights Reserved.</p>
<div class="abs social" aria-label="Social links">
  <div style="background:#3b5b9a"></div>
  <div style="background:#2aa9e0"></div>
  <div style="background:#c9202a"></div>
  <div style="background:#dd4b39"></div>
</div>

</body>
</html>
```